Der erste 100% elektrische Schulbus braucht ein wunderschönes Hingucker-Design
Ein tolles Design mit hoher Qualität und Präzision für unseren Schulbus. Ortwin ist sehr nett, hilfsbereit und proaktiv. Unser Briefing hat er kreativ zu unserer vollsten Zufriedenheit umgesetzt.
Zielgruppe
Wir glauben daran, auf kindgerechte Weise neue Fähigkeiten zu lehren und zu lernen. Wir bieten unseren Kindern einen Raum der Entdeckung und Offenheit. Unsere private Schule wird von Eltern geführt und ist von einem starken Gemeinschaftsgefühl geprägt. Sie bietet Kindern im Alter von 3 bis 12 Jahren Montessori-Bildung von höchster Qualität in Le Vallon in der französischsprachigen Schweiz (Nähe Genf).
Wir bieten einen zweisprachiges Ansatz (Englisch und Französisch) für die Kleinsten, einen dreisprachigen Ansatz (Englisch, Französisch und Deutsch) für die Älteren, frisch zubereitete Mahlzeiten und eine ganztägige Betreuung.
Unsere Schule bietet eine tägliche Schulbusverbindung von Nyon und den umliegenden Gemeinden zum Campus Le Vallon an. Wir beschäftigen unseren eigenen Fahrer und betreiben unseren eigenen Schulbus. Der Service ist für Eltern kostenlos und von den kantonalen Behörden genehmigt.
Wir glauben fest an Nachhaltigkeit und wollen ein Beispiel geben und zeigen, dass emissionsfreie Schülertransporte möglich und wirtschaftlich sind.
Aufgabenstellung
Bitte schaut Euch das Briefing im hochgeladenen PDF an.

```html
<!DOCTYPE html>
<html lang="en">
<head>
<meta charset="utf-8">
<title>Trois Cents Racines – School Bus Livery</title>
<link rel="stylesheet" href="https://fonts.googleapis.com/css2?family=Nunito:wght@400;800&display=swap">
<style>
  :root {
    --page: #ffffff;
    --panel: #535453;
    --lime: #c4d100;
    --lime-text: #8a9c00;
    --leaf: #97b81a;
    --forest: #55702a;
    --white: #ffffff;
    --ink: #2b2b2b;
    --photo-warm-a: #f4e9a8;
    --photo-warm-b: #9aad3a;
    --forest-a: #e8b634;
    --forest-b: #33401e;
  }
  * { margin: 0; padding: 0; box-sizing: border-box; }
  html, body { width: 1200px; height: 848px; overflow: hidden; background: var(--page); }
  .livery {
    position: relative;
    width: 1200px;
    height: 848px;
    font-family: "Nunito", sans-serif;
  }
  .livery-shapes { position: absolute; inset: 0; }
  .brand {
    position: absolute;
    left: 522px;
    top: 334px;
    display: flex;
    align-items: center;
    gap: 12px;
  }
  .brand-dot {
    width: 26px;
    height: 26px;
    border-radius: 50%;
    background: var(--leaf);
  }
  .brand-name {
    color: var(--white);
    font-weight: 800;
    font-size: 18px;
    line-height: 21px;
    letter-spacing: 0.4px;
  }
  .features {
    position: absolute;
    left: 525px;
    top: 444px;
    list-style: none;
    display: flex;
    flex-direction: column;
    align-items: flex-start;
    gap: 5px;
  }
  .feature {
    background: var(--lime);
    color: var(--lime-text);
    font-weight: 800;
    font-size: 15px;
    line-height: 20px;
    padding: 0 10px 0 5px;
  }
  .website {
    position: absolute;
    left: 832px;
    top: 444px;
    color: var(--leaf);
    font-weight: 800;
    font-size: 14.5px;
    letter-spacing: 0.3px;
  }
  .campus {
    position: absolute;
    left: 532px;
    top: 553px;
    color: var(--ink);
    font-weight: 400;
    font-size: 13px;
    letter-spacing: 3px;
  }
</style>
</head>
<body>
<main class="livery">
  <svg class="livery-shapes" width="1200" height="848" viewBox="0 0 1200 848">
    <defs>
      <linearGradient id="meadow-tone" x1="0" y1="0" x2="0.6" y2="1">
        <stop offset="0" stop-color="var(--photo-warm-a)"/>
        <stop offset="0.55" stop-color="#d6cf72"/>
        <stop offset="1" stop-color="var(--photo-warm-b)"/>
      </linearGradient>
      <radialGradient id="forest-tone" cx="0.5" cy="0.4" r="0.6">
        <stop offset="0" stop-color="var(--forest-a)"/>
        <stop offset="0.35" stop-color="#8a7a2a"/>
        <stop offset="1" stop-color="var(--forest-b)"/>
      </radialGradient>
    </defs>
    <rect class="title-panel" x="493" y="266" width="582" height="139" rx="10" fill="var(--panel)"/>
    <path class="photo-swing" role="img" aria-label="Photo: a happy child on a rope swing in a sunny meadow"
      d="M880,194 L1105,195 Q1120,240 1127,355 Q1065,400 1000,397 Q930,392 898,336 Q930,300 928,258 Q925,215 880,194 Z"
      fill="url(#meadow-tone)" stroke="var(--lime)" stroke-width="3"/>
    <circle class="photo-forest" role="img" aria-label="Photo: evening sun shining through forest trees"
      cx="860" cy="266" r="67" fill="url(#forest-tone)" stroke="var(--forest)" stroke-width="4"/>
  </svg>

  <div class="brand">
    <span class="brand-dot"></span>
    <p class="brand-name">Ecole Montessori<br>Trois Cents Racines</p>
  </div>

  <ul class="features">
    <li class="feature">• for kids from 3 to 12</li>
    <li class="feature">• 100% electric schoolbus</li>
    <li class="feature">• multilingual</li>
  </ul>

  <p class="website">www.troiscentsracines.ch</p>
  <p class="campus">LE VALLON</p>
</main>
</body>
</html>
```